Velk Partners Building Business Cards

We need a business card that reflects our business as "Solar Experts" in San Diego. Browse our website www.velkpartners.example our License needs to be displayed as "CSLB# 3867140" our phone number is (619) 555-0187

Save thousands on your electric bills and increase the value of your home while helping to protect the environment. Our solar installation experts will help you design the system that's right for you, using only the highest quality equipment that will look great and give you ideal performance. Our goal is to make you energy independent, and get your electric bill to 0.

Paul Osterby
(619) 555-0187
paul@velkpartners.example

Target Market(s)

Home owners in san diego looking for solar

Industry/Entity Type

Solar Energy

Contact Information for Business Card

Paul Osterby
(619) 555-0187
paul@velkpartners.example

Font styles to use
Other font styles liked:
• Use our logo font

Requirements
Must have
• License needs to be displayed as "CSLB# 3867140" our phone number is (619) 555-0187
Nice to have
• Real images of rooftop home solar in san diego
Should not have
• our business address

```html
<!DOCTYPE html>
<html lang="en">
<head>
<meta charset="utf-8">
<title>Velk Partners Building – Business Cards</title>
<link rel="stylesheet" href="https://fonts.googleapis.com/css2?family=Cinzel:wght@500;600&family=Roboto:wght@400;700&display=swap">
<style>
  :root {
    --navy: #1d3a78;
    --navy-dark: #183268;
    --gold: #f5a800;
    --white: #ffffff;
    --text-grey: #5a5a5a;
    --rule-grey: #d4d4d4;
    --backdrop: #d9d9d9;
  }
  * { box-sizing: border-box; margin: 0; padding: 0; }
  html, body {
    width: 1200px;
    height: 1000px;
    overflow: hidden;
  }
  body {
    position: relative;
    background: var(--backdrop);
    font-family: "Roboto", Arial, sans-serif;
  }
  .card {
    position: absolute;
    left: 220px;
    width: 762px;
    box-shadow: 0 3px 10px rgba(0, 0, 0, 0.25);
    overflow: hidden;
  }
  /* Front */
  .card-front {
    top: 50px;
    height: 434px;
    background: linear-gradient(120deg, var(--navy-dark) 0%, var(--navy) 55%, #2c4a8a 100%);
    color: var(--white);
  }
  .card-front .brand-name {
    position: absolute;
    top: 218px;
    left: 0;
    width: 100%;
    text-align: center;
    font-weight: 700;
    font-size: 46px;
    letter-spacing: -1px;
    color: var(--white);
  }
  .card-front .website {
    position: absolute;
    top: 374px;
    left: 0;
    width: 100%;
    text-align: center;
    font-size: 16px;
    letter-spacing: 0.3px;
  }
  /* Back */
  .card-back {
    top: 524px;
    height: 436px;
    background: var(--white);
  }
  .brand-block {
    position: absolute;
    top: 188px;
    left: 40px;
    width: 375px;
    text-align: center;
  }
  .card-back .brand-name {
    font-weight: 700;
    font-size: 30px;
    letter-spacing: -0.6px;
    line-height: 1.1;
    color: var(--navy);
  }
  .license {
    margin-top: 10px;
    font-size: 14px;
    letter-spacing: 0.6px;
    color: var(--text-grey);
  }
  .card-back .divider {
    position: absolute;
    left: 415px;
    top: 154px;
    width: 1px;
    height: 128px;
    background: var(--rule-grey);
  }
  .contact {
    position: absolute;
    left: 438px;
    top: 148px;
  }
  .contact .person-name {
    font-family: "Cinzel", Georgia, serif;
    font-weight: 600;
    font-size: 24px;
    letter-spacing: 1px;
    color: var(--navy);
    line-height: 1.1;
  }
  .contact .person-title {
    font-size: 17px;
    color: var(--text-grey);
    margin-top: 2px;
  }
  .contact-list {
    list-style: none;
    margin-top: 20px;
  }
  .contact-list li {
    display: flex;
    align-items: center;
    font-size: 17px;
    color: var(--text-grey);
    height: 24.5px;
    letter-spacing: 0.2px;
  }
  .contact-list svg {
    width: 13px;
    height: 13px;
    margin-right: 7px;
    fill: var(--gold);
    flex-shrink: 0;
  }
  .accent-bar {
    position: absolute;
    bottom: 0;
    height: 16px;
  }
  .accent-bar.navy { left: 0; width: 437px; background: var(--navy); }
  .accent-bar.gold { left: 440px; right: 0; background: var(--gold); }
</style>
</head>
<body>

  <section class="card card-front">
    <div class="brand-name">Velk Partners Building Inc</div>
    <div class="website">www.velkpartners.example</div>
  </section>

  <section class="card card-back">
    <div class="brand-block">
      <div class="brand-name">Velk Partners<br>Building Inc</div>
      <div class="license">CSLB# 3867140</div>
    </div>
    <div class="divider"></div>

    <div class="contact">
      <div class="person-name">Paul Osterby</div>
      <div class="person-title">President</div>
      <ul class="contact-list">
        <li>
          <svg viewBox="0 0 16 16" aria-hidden="true"><path d="M3.6 1.2l2.3 2.6c.3.4.3.9 0 1.3L4.8 6.3c.9 2 2.5 3.6 4.6 4.6l1.2-1.1c.4-.3.9-.3 1.3 0l2.6 2.3c.4.4.4 1 0 1.4l-1.2 1.2c-.7.7-1.8.9-2.7.5C6 13.4 2.6 10 .8 5.4.4 4.5.6 3.4 1.3 2.7l1.2-1.2c.3-.4.8-.4 1.1-.3z"/></svg>
          (619) 555-0187
        </li>
        <li>
          <svg viewBox="0 0 16 16" aria-hidden="true"><path d="M1 3h14v10H1z M1.6 3.6L8 8.6l6.4-5" stroke="#fff" stroke-width="1.2"/></svg>
          paul@velkpartners.example
        </li>
        <li>
          <svg viewBox="0 0 16 16" aria-hidden="true"><circle cx="8" cy="8" r="7"/><path d="M1 8h14M8 1c-2.5 2.5-2.5 11.5 0 14M8 1c2.5 2.5 2.5 11.5 0 14" stroke="#fff" stroke-width="1" fill="none"/></svg>
          www.velkpartners.example
        </li>
      </ul>
    </div>

    <div class="accent-bar navy"></div>
    <div class="accent-bar gold"></div>
  </section>

</body>
</html>
```